Card design for orthopaedic surgeons working as The Brightwater Joint Centre

Business cards, letterhead

Colors

Designer to choose colors to be used in the design.

Requirements
Must have
• Late addition.
• Cards letterhead must have logos of
• Crestmoor Lindell College of Surgeons
• Varenwood Bone Health Association
Nice to have
• Back of card to have space for appointment time to be added by hand and some blank space for writing incidental other notes.

```html
<!DOCTYPE html>
<html lang="en">
<head>
<meta charset="utf-8">
<title>The Brightwater Joint Centre – Stationery</title>
<link href="https://fonts.googleapis.com/css2?family=Didact+Gothic&family=Open+Sans:ital,wght@0,400;0,600;1,400&display=swap" rel="stylesheet">
<style>
:root{
  --navy:#06304a;
  --blue:#2eaef0;
  --text:#3a3a3a;
  --muted:#555;
  --bg:#dcdcdc;
  --paper:#ffffff;
}
*{box-sizing:border-box;margin:0;padding:0}
html,body{width:1200px;height:877px;overflow:hidden;background:var(--bg)}
body{position:relative;font-family:"Didact Gothic",sans-serif;color:var(--text)}
.sheet{position:absolute;background:var(--paper);overflow:hidden;box-shadow:0 1px 3px rgba(0,0,0,.12)}
.band{position:absolute;left:0;right:0;top:0;background:var(--navy)}
.band__stripe{position:absolute;left:0;right:0;height:4px;background:var(--blue)}
.card{left:118px;width:368px;height:210px;border-radius:10px}
.card--front{top:271px}
.card--front .band{height:74px}
.card--front .band__stripe{top:78px}
.card--back{top:530px}
.card__name{position:absolute;right:30px;top:26px;text-align:right}
.card__name strong{display:block;font-family:"Open Sans",sans-serif;font-weight:600;color:var(--blue);font-size:12.5px;letter-spacing:.3px}
.card__name span{display:block;font-family:"Open Sans",sans-serif;color:#fff;font-size:11px;margin-top:1px}
.brand{position:absolute;font-family:"Didact Gothic",sans-serif;white-space:nowrap}
.card .brand{left:22px;top:108px;font-size:12.5px;color:var(--navy)}
.contacts{position:absolute;left:22px;top:152px;list-style:none;font-size:9px;line-height:10.5px;color:var(--muted)}
.contacts li{display:flex;align-items:center;gap:4px}
.contacts svg{width:7px;height:7px;fill:var(--navy)}
.address{position:absolute;left:236px;top:160px;font-size:9px;line-height:10.5px;color:var(--muted)}
.address .web{margin-top:6px}
.appt{font-family:"Open Sans",sans-serif;color:var(--blue)}
.appt__title{position:absolute;left:0;right:0;top:29px;text-align:center;font-size:15px;font-weight:600}
.appt__line{position:absolute;font-size:11px;white-space:nowrap}
.dots{color:#777;font-size:8px}
.small{font-size:8px}
.days{position:absolute;left:24px;right:24px;top:140px;display:flex;justify-content:space-between;font-size:9.5px}
.days span{display:flex;align-items:center;gap:4px}
.box{width:9px;height:8px;border:1.3px solid var(--navy);display:inline-block}
.appt__note{position:absolute;left:0;right:0;top:176px;text-align:center;font-size:7.5px;font-style:italic;color:#444;line-height:10.5px}
.letter{left:557px;top:69px;width:527px;height:741px}
.letter .band{height:96px}
.letter .band__stripe{top:101px}
.letter .brand{right:45px;top:40px;font-size:12.5px;color:#fff}
.letter__body{position:absolute;left:46px;top:206px;width:438px}
.salutation{font-size:14px;color:var(--muted);margin-bottom:19px}
.letter__body p{font-size:7.6px;line-height:11.4px;color:#444;margin-bottom:11.4px;text-align:justify}
.signoff{margin-top:21px}
.signature{display:block;width:62px;height:26px;margin-top:12px;background:#e6e9ec;border-radius:3px}
.letter__footer{position:absolute;left:0;right:0;top:693px;text-align:center;font-size:7.6px;line-height:10px;color:#555}
</style>
</head>
<body>

<section class="sheet card card--front" aria-label="Business card front">
  <div class="band"></div>
  <div class="band__stripe"></div>
  <div class="card__name"><strong>DANIEL HARTLEY</strong><span>President</span></div>
  <div class="brand">The Brightwater Joint Centre</div>
  <ul class="contacts">
    <li><svg viewBox="0 0 10 10"><path d="M2 0l2 2-1 1.5c.8 1.6 1.9 2.7 3.5 3.5L8 6l2 2-1.5 2C4 9.5.5 6 0 1.5Z"/></svg>555-214-0871</li>
    <li><svg viewBox="0 0 10 10"><path d="M2 0h6v10H2Zm1 1v7h4V1Z"/></svg>555-318-2264</li>
    <li><svg viewBox="0 0 10 10"><path d="M2 0h6v3H2ZM0 4h10v4H0Zm2 3h6v3H2Z"/></svg>555-402-7719</li>
    <li><svg viewBox="0 0 10 10"><path d="M0 2h10v6H0Z"/></svg>daniel@brightwaterjoint.com</li>
  </ul>
  <div class="address">
    <div>42 Willowmere Road</div>
    <div>Brightwater, 60218</div>
    <div class="web">www.brightwaterjoint.com</div>
  </div>
</section>

<section class="sheet card card--back appt" aria-label="Appointment card">
  <h2 class="appt__title">Next Appointment</h2>
  <div class="appt__line" style="left:23px;top:68px"><span class="dots">........................................................................................................</span>has an apppointment</div>
  <div class="appt__line" style="left:21px;top:102px">Date : &nbsp;<span class="dots">.........................................................</span> Time : <span class="dots">.................................</span> <span class="small">AM/PM</span></div>
  <div class="days">
    <span>Sun <i class="box"></i></span><span>Mon <i class="box"></i></span><span>Tue <i class="box"></i></span><span>Wed <i class="box"></i></span><span>Thu <i class="box"></i></span><span>Fri <i class="box"></i></span><span>Sat <i class="box"></i></span>
  </div>
  <p class="appt__note">Please give me 24 hours notice if you are unable to keep your appointment or<br>a cancellation fee may be charged.</p>
</section>

<section class="sheet letter" aria-label="Letterhead">
  <div class="band"></div>
  <div class="band__stripe"></div>
  <div class="brand">The Brightwater Joint Centre</div>
  <div class="letter__body">
    <div class="salutation">Dear Mr. Calloway,</div>
    <p>Lorem ipsum dolor sit amet, consectetur adipiscing elit. Donec orci purus, luctus vitae dignissim eu, iaculis sed purus. Vivamus faucibus, ipsum nec aliquet viverra, leo mauris condimentum ligula, sit amet sagittis enim ligula quis arcu. Nam egestas tortor id nisi porttitor mattis. In tortor ante, ultricies in suscipit a, tempus non massa. Vivamus et auctor mi. Fusce vel massa nulla. Phasellus nec eros mauris, et scelerisque orci.</p>
    <p>Donec malesuada orci vitae nulla accumsan porta a id massa. Quisque accumsan iaculis magna sit amet fringilla. Maecenas consequat, magna eget tincidunt semper, odio nibh rutrum mi, id feugiat ante nisi eu risus. Vestibulum nunc orci, rhoncus a placerat in, ultricies in mi. Cras mattis varius eros, vel fringilla nisi suscipit eget. Quisque scelerisque sagittis nulla at porttitor.</p>
    <p>Sed id augue vitae urna euismod commodo aliquet a quam. Pellentesque arcu velit, cursus et malesuada ut, consequat et diam. Nullam erat sem, rhoncus id ullamcorper vitae, rhoncus et arcu. In ultricies ultricies nulla, ut rutrum nisi iaculis at. Donec eu magna a metus ornare faucibus. Fusce aliquet faucibus ultricies. Morbi semper, est id tincidunt gravida, sem arcu adipiscing lacus, ac bibendum nulla leo eu purus. Quisque nec diam sed risus consectetur accumsan quis quis nibh. Vestibulum id purus lorem.</p>
    <p>It is a long established fact that a reader will be distracted by the readable content of a page when looking at its layout. The point of using Lorem Ipsum is that it has a more-or-less normal distribution of letters, as opposed to using 'Content here, content here', making it look like readable English. Many desktop publishing packages</p>
    <p class="signoff">Sincerely,</p>
    <span class="signature" role="img" aria-label="Handwritten signature"></span>
  </div>
  <div class="letter__footer">
    <div>42 Willowmere Road, Brightwater, 60218 &nbsp;·&nbsp; 555-214-0871 &nbsp;·&nbsp; 555-318-2264</div>
    <div>555-402-7719 &nbsp;·&nbsp; daniel@brightwaterjoint.com &nbsp;·&nbsp; www.brightwaterjoint.com</div>
  </div>
</section>

</body>
</html>
```